A clean crisp business card for a Landscape Construction company. Designed to be easy to read contact/ info and also be appealing/interesting, unlike a traditional business card.

Industry/Entity Type

Landscape Construction

Contact Information for Business Card

Company name : Brambleford Landscape Construction, phone number: (877) 62Vista, website:Bramblefordyards.example, Email, sales@bramblefordyards.example

Requirements
Nice to have
• Luxurious finishes/ details…. Icons or emblems next to contact info
Should not have
• Clipart or general pictures

```html
<!DOCTYPE html>
<html lang="en">
<head>
<meta charset="utf-8">
<title>Brambleford Landscape Construction – Business Card</title>
<link rel="stylesheet" href="https://fonts.googleapis.com/css2?family=Cinzel:wght@700&family=Arimo:ital,wght@0,400;1,400&display=swap">
<style>
  :root {
    --page-bg: #e9e9e7;
    --card-bg: #262626;
    --brand-blue: #1f6fc6;
    --brand-green: #8cc63f;
    --text-white: #ffffff;
  }
  * { margin: 0; padding: 0; box-sizing: border-box; }
  html, body {
    width: 1200px; height: 900px; overflow: hidden;
    background: var(--page-bg);
  }
  .canvas {
    position: relative; width: 1200px; height: 900px;
  }
  .business-card {
    position: absolute; left: 75px; top: 150px;
    width: 1050px; height: 600px;
    background: var(--card-bg);
    border-radius: 28px;
  }
  .brand-lockup {
    position: absolute; left: 380px; top: 110px;
    display: flex; align-items: center; gap: 22px;
  }
  .brand-dot {
    width: 34px; height: 34px; border-radius: 50%;
    background: var(--brand-green);
    flex: none;
  }
  .brand-name {
    font-family: "Cinzel", serif; font-weight: 700;
    font-size: 38px; line-height: 1.15;
    color: var(--brand-blue);
    letter-spacing: 1px;
  }
  .person {
    position: absolute; right: 590px; top: 300px;
    text-align: right;
  }
  .person-name {
    font-family: "Cinzel", serif; font-weight: 700;
    font-size: 40px; letter-spacing: 1px; white-space: nowrap;
  }
  .person-name .first { color: var(--brand-blue); }
  .person-name .last { color: var(--brand-green); }
  .person-role {
    font-family: "Arimo", sans-serif; font-style: italic;
    font-size: 26px; color: var(--text-white); margin-top: 6px;
  }
  .divider {
    position: absolute; left: 490px; top: 290px;
    width: 2px; height: 160px; background: var(--brand-blue);
  }
  .contact-list {
    position: absolute; left: 520px; top: 290px;
    list-style: none;
  }
  .contact-item {
    display: flex; align-items: center; gap: 14px;
    font-family: "Arimo", sans-serif; font-size: 26px;
    color: var(--text-white); height: 52px; white-space: nowrap;
  }
  .contact-icon { width: 24px; height: 24px; flex: none; }
  .contact-icon * { fill: var(--brand-green); }
</style>
</head>
<body>
<main class="canvas">
  <section class="business-card">
    <div class="brand-lockup">
      <span class="brand-dot"></span>
      <div class="brand-name">Brambleford<br>Landscape Construction</div>
    </div>

    <div class="person">
      <div class="person-name"><span class="first">Owen</span> <span class="last">Hartley</span></div>
      <div class="person-role">Founder</div>
    </div>

    <div class="divider"></div>

    <ul class="contact-list">
      <li class="contact-item">
        <svg class="contact-icon" viewBox="0 0 24 24" aria-hidden="true"><path d="M6.6 10.8a15.1 15.1 0 0 0 6.6 6.6l2.2-2.2a1 1 0 0 1 1-.25 11.4 11.4 0 0 0 3.6.57 1 1 0 0 1 1 1V20a1 1 0 0 1-1 1A17 17 0 0 1 3 4a1 1 0 0 1 1-1h3.5a1 1 0 0 1 1 1c0 1.25.2 2.45.57 3.57a1 1 0 0 1-.25 1z"/></svg>
        <span>(877) 62Vista</span>
      </li>
      <li class="contact-item">
        <svg class="contact-icon" viewBox="0 0 24 24" aria-hidden="true"><path d="M2 5h20v2l-10 6L2 7z"/><path d="M2 9.3l10 6 10-6V19H2z"/></svg>
        <span>sales@bramblefordyards.example</span>
      </li>
      <li class="contact-item">
        <svg class="contact-icon" viewBox="0 0 24 24" aria-hidden="true"><path fill-rule="evenodd" d="M12 2a10 10 0 1 0 0 20 10 10 0 0 0 0-20zm-1 2.1A8 8 0 0 0 4.1 11H8c.1-2.6.9-5 3-6.9zm2 0c2.1 1.9 2.9 4.3 3 6.9h3.9A8 8 0 0 0 13 4.1zM10 11h4c-.1-2.2-.8-4.1-2-5.6-1.2 1.5-1.9 3.4-2 5.6zm0 2c.1 2.2.8 4.1 2 5.6 1.2-1.5 1.9-3.4 2-5.6zm-5.9 0A8 8 0 0 0 11 19.9c-2.1-1.9-2.9-4.3-3-6.9zm11.9 0c-.1 2.6-.9 5-3 6.9a8 8 0 0 0 6.9-6.9z"/></svg>
        <span>bramblefordyards.example</span>
      </li>
    </ul>
  </section>
</main>
</body>
</html>
```